Web Design Project - brivolta

I'm building an agency for marketing solutions but also medical education and patients education for pharmaceutical companies, medical societies and patient advocacy groups. We want to be perceived as the most innovative in the market. We work through design thinking solutions for campaigns and services.
I love some websites based on Swiss style design like www.quorlinex.com
We are a small group of designers, physicians and creatives working together to deliver the best experiences in our market.
We decided to also use pixel bazaar expecting that we maybe found a great idea we didn't thought about yet.

I'm extending it for more 2 weeks

Reason: I need the best design you can. Only PSD. No code needed. Love Swiss style, like velmora 5 and quorlinex.com I'm extending the deadline until get something great. Willing to extend as much as needed.

Target Market(s)

Pharmaceutical companies, physicians, medical societies, patients advocacy groups

Industry/Entity Type

Pharmaceutical

Font styles to use
Other font styles liked:
• Helvetia family

Colors

Designer to choose colors to be used in the design.

Requirements
Must have
• Must be innovative like www.quorlinex.com
Nice to have
• Cool menus
Should not have
• Not to appear too much Comercial. We like to be a boutique in this market. Craftsmen working with less clients at time but delivering precious stones.

```html
<!DOCTYPE html>
<html lang="en">
<head>
<meta charset="utf-8">
<title>Brivolta</title>
<link href="https://fonts.googleapis.com/css2?family=Oswald:wght@500&family=Roboto:wght@300;400&display=swap" rel="stylesheet">
<style>
:root{
  --teal:#5ccfcb;
  --teal-soft:#6fd0cc;
  --ink:#3d3d3d;
  --muted:#777;
  --black:#000;
  --white:#fff;
  --sky:#3fb3e8;
  --friendly:#3d70b2;
  --chirper:#5bbdf0;
  --pinwall:#c9222b;
  --orbit:#3f7cc2;
  --rss:#e8531d;
  --mail:#18c1cc;
}
*{margin:0;padding:0;box-sizing:border-box}
html,body{width:685px;height:1200px;overflow:hidden;background:var(--black);font-family:'Roboto',Arial,sans-serif}
.page{position:relative;width:685px;height:1200px}
.header{position:absolute;left:0;top:0;width:685px;height:46px;background:var(--white)}
.logo{position:absolute;left:31px;top:7px;font-family:'Oswald',sans-serif;font-weight:500;font-size:25px;color:var(--teal);letter-spacing:-.3px}
.nav{position:absolute;top:17px;font-size:11px;color:var(--ink)}
.search{position:absolute;left:517px;top:17px}
.divider{position:absolute;left:543px;top:0;width:1px;height:46px;background:#e5e5e5}
.dot{position:absolute;top:19px;width:8px;height:8px;border-radius:50%;background:#bbb}
.menu-btn{position:absolute;left:616px;top:0;width:38px;height:46px;background:var(--teal)}
.menu-btn span{position:absolute;left:13px;width:13px;height:2px;background:var(--white)}
.slider{position:absolute;left:32px;top:75px;width:622px;height:297px;background:linear-gradient(100deg,#8e8e8c 0%,#b9aea2 45%,#6a5a50 70%,#9b928a 100%)}
.slider-title{position:absolute;left:62px;top:78px;font-family:'Oswald',sans-serif;font-weight:500;font-size:32px;color:var(--white);letter-spacing:-.5px}
.slider-text{position:absolute;left:64px;top:130px;width:250px;font-size:8px;line-height:15px;color:#f2f2f2;font-weight:300}
.view-more{position:absolute;left:63px;top:203px;width:106px;height:32px;border:1px solid var(--white);color:var(--white);font-size:10px;text-align:center;line-height:30px}
.arrow{position:absolute;top:130px;width:21px;height:31px;background:var(--white)}
.card{position:absolute;background:var(--white)}
.photo{position:absolute}
.badge{position:absolute;width:24px;height:24px;background:var(--sky)}
.card-title{position:absolute;font-size:23px;line-height:29px;color:var(--ink);font-weight:400}
.card-text{position:absolute;font-size:7.6px;line-height:15px;color:var(--muted);width:140px}
.society{position:absolute;left:32px;top:806px;width:187px;height:187px;background:linear-gradient(160deg,#6fd3ce,#5cc6c4)}
.society h3{position:absolute;left:22px;top:35px;font-size:23px;line-height:29px;color:var(--white);font-weight:400}
.society p{position:absolute;left:22px;top:95px;width:160px;font-size:7.6px;line-height:15px;color:var(--white)}
.society .go{position:absolute;left:22px;top:150px;width:20px;height:20px;border-radius:50%;background:var(--white)}
.tile{position:absolute;top:1020px;width:96px;height:96px;color:var(--white);text-align:center}
.tile svg{position:absolute;left:23px;top:15px}
.tile span{position:absolute;left:0;width:96px;top:67px;font-size:14px;font-weight:300}
.footer-line{position:absolute;left:0;top:1150px;width:685px;height:1px;background:#1c1c1c}
.copyright{position:absolute;left:0;width:685px;top:1171px;text-align:center;font-size:8px;color:#8a8a8a}
</style>
</head>
<body>
<div class="page">
  <header class="header">
    <div class="logo">Brivolta</div>
    <nav>
      <span class="nav" style="left:283px">Home</span>
      <span class="nav" style="left:337px">About</span>
      <span class="nav" style="left:390px">Projects</span>
      <span class="nav" style="left:453px">Contact</span>
    </nav>
    <svg class="search" width="11" height="11" viewBox="0 0 11 11"><circle cx="4.5" cy="4.5" r="3.5" fill="none" stroke="#aaa" stroke-width="1.2"/><line x1="7" y1="7" x2="10" y2="10" stroke="#aaa" stroke-width="1.4"/></svg>
    <div class="divider"></div>
    <div class="dot" style="left:556px"></div>
    <div class="dot" style="left:574px"></div>
    <div class="dot" style="left:593px"></div>
    <div class="menu-btn"><span style="top:18px"></span><span style="top:22px"></span><span style="top:26px"></span></div>
  </header>

  <section class="slider" role="img" aria-label="Smiling businesswoman in front of a team meeting">
    <h1 class="slider-title">Marketing Solutions</h1>
    <p class="slider-text">Lorem ipsum dolor sit amet, consectetur adipiscing elit, sed do eiusmod tempor incididunt ut labore et dolore magna aliqua. Ut enim ad minim veniam, quis nostrud exercitation ullamco laboris nisi ut</p>
    <div class="view-more">VIEW MORE</div>
    <div class="arrow" style="left:0"><svg width="21" height="31"><path d="M12 12l-3.5 3.5L12 19" fill="none" stroke="#333" stroke-width="1.8"/></svg></div>
    <div class="arrow" style="left:601px"><svg width="21" height="31"><path d="M9 12l3.5 3.5L9 19" fill="none" stroke="#333" stroke-width="1.8"/></svg></div>
  </section>

  <article class="card" style="left:32px;top:400px;width:383px;height:187px">
    <div class="badge" style="left:0;top:21px"></div>
    <h2 class="card-title" style="left:41px;top:18px">Medical<br>Education</h2>
    <p class="card-text" style="left:42px;top:85px">Lorem ipsum dolor sit amet, con-sectetur adipiscing elit, sed do eius-mod tempor incididunt ut labore et dolore magna aliqua. Ut enim ad minim veniam, quis nostrud exercita-tion ullamco laboris nisi ut</p>
    <div class="photo" role="img" aria-label="Doctor working on a laptop in a clinic" style="left:196px;top:0;width:187px;height:187px;background:linear-gradient(135deg,#dfe8e8,#c9d6d9 50%,#f2f4f4)"></div>
  </article>

  <article class="card" style="left:431px;top:400px;width:223px;height:187px">
    <div class="badge" style="left:0;top:21px"></div>
    <h2 class="card-title" style="left:41px;top:18px">Pharmaceutical<br>Companies</h2>
    <p class="card-text" style="left:42px;top:85px">Lorem ipsum dolor sit amet, con-sectetur adipiscing elit, sed do eius-mod tempor incididunt ut labore et dolore magna aliqua. Ut enim ad minim veniam, quis nostrud exercita-tion ullamco laboris nisi ut</p>
  </article>
  <div class="photo" role="img" aria-label="Laboratory research with pipette and flasks" style="left:431px;top:587px;width:223px;height:200px;background:linear-gradient(135deg,#bfe0f0,#3c93c8 55%,#1a5f93)"></div>

  <article class="card" style="left:32px;top:599px;width:383px;height:187px">
    <div class="photo" role="img" aria-label="Nurse comforting a senior patient" style="left:0;top:0;width:186px;height:187px;background:linear-gradient(135deg,#dcd8d2,#eee9e3 50%,#c7c0b8)"></div>
    <div class="badge" style="left:186px;top:22px"></div>
    <h2 class="card-title" style="left:228px;top:19px">Patients<br>Education</h2>
    <p class="card-text" style="left:229px;top:84px">Lorem ipsum dolor sit amet, con-sectetur adipiscing elit, sed do eius-mod tempor incididunt ut labore et dolore magna aliqua. Ut enim ad minim veniam, quis nostrud exercita-tion ullamco laboris nisi ut</p>
  </article>

  <section class="society">
    <h3>Medical<br>Societies</h3>
    <p>Lorem ipsum dolor sit amet, consectetur adipiscing elit, sed do eiusmod tempor incididunt ut labore et dolore magna</p>
    <div class="go"><svg width="20" height="20"><path d="M9 7l3 3-3 3" fill="none" stroke="#6fd0cc" stroke-width="1.6"/></svg></div>
  </section>

  <article class="card" style="left:237px;top:806px;width:417px;height:187px">
    <div class="photo" role="img" aria-label="Doctor talking with a patient at a desk" style="left:0;top:0;width:220px;height:187px;background:linear-gradient(120deg,#e6e6e4,#f4f4f2 50%,#b9c6d8)"></div>
    <div class="badge" style="left:220px;top:22px"></div>
    <h2 class="card-title" style="left:261px;top:19px">Patient<br>Advocacy</h2>
    <p class="card-text" style="left:262px;top:84px">Lorem ipsum dolor sit amet, con-sectetur adipiscing elit, sed do eius-mod tempor incididunt ut labore et dolore magna aliqua. Ut enim ad minim veniam, quis nostrud exercita-tion ullamco laboris nisi ut</p>
  </article>

  <div class="tile" style="left:32px;background:var(--friendly)"><svg width="50" height="50"><circle cx="25" cy="25" r="24" fill="none" stroke="#fff" stroke-width="2"/></svg><span>friendly</span></div>
  <div class="tile" style="left:137px;background:var(--chirper)"><svg width="50" height="50"><circle cx="25" cy="25" r="24" fill="none" stroke="#fff" stroke-width="2"/></svg><span>chirper</span></div>
  <div class="tile" style="left:243px;background:var(--pinwall)"><svg width="50" height="50"><circle cx="25" cy="25" r="24" fill="none" stroke="#fff" stroke-width="2"/></svg><span>Pinwall</span></div>
  <div class="tile" style="left:348px;background:var(--orbit)"><svg width="50" height="50"><circle cx="25" cy="25" r="24" fill="none" stroke="#fff" stroke-width="2"/></svg><span>orbit Plus</span></div>
  <div class="tile" style="left:453px;background:var(--rss)"><svg width="50" height="50"><circle cx="25" cy="25" r="24" fill="none" stroke="#fff" stroke-width="2"/><circle cx="18" cy="32" r="2.5" fill="#fff"/><path d="M16 24a10 10 0 0 1 10 10M16 17a17 17 0 0 1 17 17" fill="none" stroke="#fff" stroke-width="3"/></svg><span>RSS</span></div>
  <div class="tile" style="left:558px;background:var(--mail)"><svg width="50" height="50"><circle cx="25" cy="25" r="24" fill="none" stroke="#fff" stroke-width="2"/><rect x="13" y="17" width="24" height="17" rx="2" fill="#fff"/><path d="M14 18l11 9 11-9" fill="none" stroke="#18c1cc" stroke-width="1.8"/></svg><span>Email</span></div>

  <div class="footer-line"></div>
  <footer class="copyright">©2013 - 2014 Brivolta., All Rights Reserved.</footer>
</div>
</body>
</html>
```